Local Flower Farm Needs Business Card Design

I need business cards designed for a flower farm based in Eudora, Kansas.
Business Info:
We are a local cut flower farm located in Eudora, Kansas, founded by Corinne Haldwick. What started as a passion for agriculture and search for more joy in daily life has blossomed into a small business dedicated to providing the community with beautiful, fresh, and sustainable flowers. We specialize in local, seasonal blooms, ensuring that every petal reflects the care and dedication we pour into our craft. Our mission is to deliver the highest quality flowers directly to our customers through local farmers markets and to florists who share our commitment to sustainability. Join us in celebrating the beauty of nature, one bloom at a time!
Contact Details:
Corinne Haldwick
Owner
Phone 913-555-0147
Facebook: Rosalind Thorpe Gardens
Instagram: @RosalindThorpeGardens
Website: RosalindThorpeGardens.example
Target Market(s)
Wholesale to Florists and Direct to Consumer via Farmers Market
Industry/Entity Type
Florist, Farm
Contact Information for Business Card
Name, Contact Info, Logo
Look and feel
Each slider illustrates characteristics of the customer's brand and the style your logo design should communicate.

```html
<!DOCTYPE html>
<html lang="en">
<head>
<meta charset="utf-8">
<title>Rosalind Thorpe Gardens — Business Card</title>
<link rel="stylesheet" href="https://fonts.googleapis.com/css2?family=Montserrat:wght@400;500;700&display=swap">
<style>
  :root {
    --backdrop: #8f9090;
    --card-front: #e9e9ec;
    --card-back: #08272d;
    --ink: #0c0c0e;
    --ink-soft: #1f2c30;
    --emboss: #0f3a41;
  }
  html, body {
    margin: 0;
    padding: 0;
    width: 1200px;
    height: 1200px;
    overflow: hidden;
    background: var(--backdrop);
    font-family: "Montserrat", Arial, sans-serif;
  }
  .canvas {
    position: relative;
    width: 1200px;
    height: 1200px;
  }
  .card {
    position: absolute;
    left: 233px;
    width: 748px;
    height: 416px;
    box-sizing: border-box;
  }
  .card--front { top: 101px; background: var(--card-front); color: var(--ink); }
  .card--back { top: 667px; background: var(--card-back); }

  .holder { position: absolute; left: 49px; top: 44px; }
  .holder__name { margin: 0; font-weight: 700; font-size: 25px; line-height: 1.1; letter-spacing: 0.2px; }
  .holder__role { margin: 2px 0 0; font-weight: 400; font-size: 19px; }

  .contacts {
    position: absolute;
    left: 49px;
    top: 212px;
    margin: 0;
    padding: 0;
    list-style: none;
  }
  .contacts__item {
    display: flex;
    align-items: center;
    height: 33px;
    font-size: 19.5px;
    font-weight: 400;
    letter-spacing: 0.2px;
  }
  .contacts__icon {
    width: 24px;
    height: 24px;
    margin-right: 9px;
    flex: none;
  }

  .brand-mark {
    position: absolute;
    display: flex;
    align-items: center;
    justify-content: center;
    text-align: center;
    border-radius: 50%;
    box-sizing: border-box;
    font-family: "Montserrat", Arial, sans-serif;
    font-weight: 500;
    text-transform: uppercase;
    letter-spacing: 2px;
    line-height: 1.35;
  }
  .brand-mark--front {
    left: 531px; top: 42px;
    width: 168px; height: 168px;
    border: 1.5px solid var(--ink-soft);
    color: var(--ink-soft);
    font-size: 15px;
  }
  .brand-mark--back {
    left: 274px; top: 106px;
    width: 204px; height: 204px;
    border: 2px solid var(--emboss);
    color: var(--emboss);
    font-size: 18px;
  }
</style>
</head>
<body>
<main class="canvas">

  <section class="card card--front" aria-label="Business card front">
    <div class="holder">
      <h1 class="holder__name">Corinne Haldwick</h1>
      <p class="holder__role">Owner</p>
    </div>

    <div class="brand-mark brand-mark--front">Rosalind<br>Thorpe<br>Gardens</div>

    <ul class="contacts">
      <li class="contacts__item">
        <svg class="contacts__icon" viewBox="0 0 24 24" aria-hidden="true">
          <circle cx="12" cy="12" r="12" fill="var(--ink)"/>
          <path d="M8.2 6.5l1.8-.4 1.1 2.7-1.3 1c.6 1.4 1.7 2.5 3.1 3.1l1-1.3 2.7 1.1-.4 1.8c-.1.5-.6.8-1.1.8C10.6 15.1 7.9 12.4 7.4 7.6c0-.5.3-1 .8-1.1z" fill="#fff"/>
        </svg>
        913-555-0147
      </li>
      <li class="contacts__item">
        <svg class="contacts__icon" viewBox="0 0 24 24" aria-hidden="true">
          <circle cx="12" cy="12" r="12" fill="var(--ink)"/>
          <rect x="6.5" y="8" width="11" height="8" rx="1" fill="#fff"/>
          <path d="M6.8 8.6L12 12.4l5.2-3.8" fill="none" stroke="var(--ink)" stroke-width="1.4"/>
        </svg>
        corinne@rosalindthorpegardens.example
      </li>
      <li class="contacts__item">
        <svg class="contacts__icon" viewBox="0 0 24 24" aria-hidden="true">
          <circle cx="12" cy="12" r="12" fill="var(--ink)"/>
          <circle cx="12" cy="12" r="6" fill="none" stroke="#fff" stroke-width="1.4"/>
          <ellipse cx="12" cy="12" rx="2.6" ry="6" fill="none" stroke="#fff" stroke-width="1.2"/>
          <path d="M6 12h12" stroke="#fff" stroke-width="1.2"/>
        </svg>
        www.rosalindthorpegardens.example
      </li>
      <li class="contacts__item">
        <svg class="contacts__icon" viewBox="0 0 24 24" aria-hidden="true">
          <circle cx="12" cy="12" r="12" fill="var(--ink)"/>
        </svg>
        Rosalind Thorpe Gardens
      </li>
      <li class="contacts__item">
        <svg class="contacts__icon" viewBox="0 0 24 24" aria-hidden="true">
          <circle cx="12" cy="12" r="12" fill="var(--ink)"/>
        </svg>
        @RosalindThorpeGardens
      </li>
    </ul>
  </section>

  <section class="card card--back" aria-label="Business card back">
    <div class="brand-mark brand-mark--back">Rosalind<br>Thorpe<br>Gardens</div>
  </section>

</main>
</body>
</html>
```